BQR, LLC Original

I need a business card design for a new company in Gaithersburg, MD. Though the name of the company is Wiremasters Of Northfield (BQR) we specialize in commercial kitchen ventilation systems as a complete turnkey project or as a service provider. We can design the entire system including the hoods, fans, ductwork, and fire system. We also specialize in fire alarm service, design, install and inspection. We are experts on any Ventaro Dynamics equipment including Pulsar VXM, Pulsar Canopies, EMS controls, Standard controls, PCU filtration and Make-up Air units with heaters and cooling. We can repair/retrofit old water wash hood systems as well. We are experts with local code requirements and upgrades.

Industry/Entity Type

Business

Contact Information for Business Card

Dale Pruitt, Wiremasters Of Northfield, LLC; 240-555-0187 Cell, Millbrook, MD 20914. Dalep@wiremastersnorthfield.example

```html
<!DOCTYPE html>
<html lang="en">
<head>
<meta charset="utf-8">
<title>Of Northfield, LLC – Business Card</title>
<link href="https://fonts.googleapis.com/css2?family=Tinos&family=Arimo&display=swap" rel="stylesheet">
<style>
  :root {
    --canvas-bg: #e9e6e2;
    --card-black: #000000;
    --card-white: #ffffff;
    --brand-yellow: #f2d21c;
    --ink: #111111;
  }
  * { margin: 0; padding: 0; box-sizing: border-box; }
  html, body {
    width: 1200px;
    height: 914px;
    overflow: hidden;
    background: var(--canvas-bg);
  }
  .canvas {
    width: 1200px;
    height: 914px;
    display: flex;
    flex-direction: column;
    align-items: center;
    justify-content: center;
    gap: 40px;
  }
  .card {
    width: 700px;
    height: 400px;
    display: flex;
    box-shadow: 0 6px 18px rgba(0,0,0,0.18);
  }
  .card-front {
    background: var(--card-black);
    align-items: center;
    justify-content: center;
    padding-top: 60px;
  }
  .brand-mark {
    display: flex;
    align-items: center;
    gap: 14px;
    font-family: "Tinos", serif;
    color: var(--brand-yellow);
    font-size: 46px;
    letter-spacing: 0.5px;
    white-space: nowrap;
  }
  .brand-mark--small { font-size: 30px; gap: 10px; }
  .brand-dot {
    width: 18px;
    height: 18px;
    border-radius: 50%;
    background: var(--brand-yellow);
    flex: none;
  }
  .brand-mark--small .brand-dot { width: 12px; height: 12px; }
  .card-back-brand {
    width: 48%;
    background: var(--card-black);
    display: flex;
    align-items: center;
    justify-content: center;
    padding-top: 40px;
  }
  .card-back-details {
    flex: 1;
    background: var(--card-white);
    display: flex;
    flex-direction: column;
    align-items: center;
    justify-content: center;
    font-family: "Arimo", sans-serif;
    color: var(--ink);
    text-align: center;
  }
  .contact-name {
    color: var(--brand-yellow);
    font-size: 30px;
    line-height: 1;
  }
  .contact-role {
    font-size: 14px;
    margin-top: 2px;
    margin-bottom: 52px;
  }
  .contact-line {
    font-size: 17px;
    line-height: 1.55;
  }
</style>
</head>
<body>
  <main class="canvas">
    <section class="card card-front">
      <div class="brand-mark">
        <span class="brand-dot"></span>
        <span class="brand-name">Of Northfield, LLC</span>
      </div>
    </section>

    <section class="card card-back">
      <div class="card-back-brand">
        <div class="brand-mark brand-mark--small">
          <span class="brand-dot"></span>
          <span class="brand-name">Of Northfield, LLC</span>
        </div>
      </div>
      <div class="card-back-details">
        <p class="contact-name">Dale Pruitt</p>
        <p class="contact-role">Electricians</p>
        <p class="contact-line">240-555-0187</p>
        <p class="contact-line">Millbrook, MD 20914</p>
        <p class="contact-line">Dalep@wiremastersnorthfield.example</p>
      </div>
    </section>
  </main>
</body>
</html>
```